brightquokka.net we need a webpage designed for our new product

We need a webpage designed for our new range of products from our new brand. We have had a logo designed on sketchharbor (see attached) and we want to keep to this theme. Our first product is a range of affordable app controlled LED lightbulbs.

I have added some photos that we think is good inspirational material and would be good as a background to this website, but we want the site to look modern but not conventional. We would like something that makes our company look quirky not corporate.

Thats it

Target Market(s)

Our product is being stocked by big name online retailers in the UK, the page will get link through hits from our app. Our target market is gadget freaks of all ages.

Industry/Entity Type

It Company

Requirements
Must have
• We are going to need a help page, text to be uploaded next few days.

We need a contact page.

design my work on iOS and Android as most people will access page through their handset or tablet.
Should not have
• We do not want anything too corporate.

```html
<!DOCTYPE html>
<html lang="en">
<head>
<meta charset="utf-8">
<title>Bright Quokka — App Controlled LED Bulbs</title>
<link href="https://fonts.googleapis.com/css2?family=Raleway:wght@400;500;600;700&family=Open+Sans:wght@400;600;700&display=swap" rel="stylesheet">
<style>
:root{
  --green:#3aa646;
  --green-bright:#3bb54a;
  --ink:#222;
  --text:#555;
  --nav:#444;
  --muted-bg:#f2f2f2;
  --white:#fff;
  --line:#d6d6d6;
  --footer:#111;
}
*{margin:0;padding:0;box-sizing:border-box}
html,body{width:719px;height:1200px;overflow:hidden;background:var(--white)}
body{font-family:"Open Sans",Arial,sans-serif;color:var(--text);position:relative}
.abs{position:absolute}
.heading{font-family:"Raleway",Arial,sans-serif;font-weight:400;color:var(--ink)}

/* header */
.site-header{position:absolute;left:0;top:0;width:719px;height:110px;background:var(--white)}
.brand{left:66px;top:30px;display:flex;align-items:center;gap:8px}
.brand-mark{width:22px;height:22px;border-radius:50%;background:var(--green)}
.brand-name{font-family:"Raleway",Arial,sans-serif;font-weight:700;font-size:13px;color:var(--green);letter-spacing:.5px}
.contact-line{right:66px;font-size:10px;display:flex;align-items:center;gap:6px}
.contact-email{top:16px;color:var(--ink)}
.contact-phone{top:31px;color:var(--green)}
.main-nav{top:63px;right:66px;display:flex;gap:0}
.main-nav a{font-size:9.5px;color:var(--nav);text-decoration:none;margin-left:42px;position:relative;padding-bottom:5px}
.main-nav a.active{color:var(--ink)}
.main-nav a.active::after{content:"";position:absolute;left:0;right:0;bottom:0;height:2px;background:var(--green)}

/* hero */
.hero{left:0;top:110px;width:719px;height:262px;background:linear-gradient(100deg,#3b3a37 0%,#4d4a44 40%,#2e2d2b 100%)}
.hero-product{left:505px;top:0;width:158px;height:262px;background:linear-gradient(180deg,#2f6b3a 0%,#3a3a3a 40%,#d8dde4 75%,#f0e2bd 100%);border-radius:18px 18px 0 0}
.hero-welcome{left:67px;top:50px;font-size:26px;color:var(--white);font-weight:400}
.hero-title{left:67px;top:84px;font-size:35px;color:var(--white);font-weight:400}
.hero-sub{left:67px;top:128px;font-size:16px;line-height:18px;color:var(--white);font-weight:400;width:300px}
.btn-solid{background:var(--green-bright);color:var(--white);text-decoration:none;display:flex;align-items:center;justify-content:center}
.hero-btn{left:67px;top:180px;width:88px;height:24px;font-family:"Raleway",Arial,sans-serif;font-weight:600;font-size:11.5px}

/* what we do */
.what-we-do{left:0;top:372px;width:719px;height:189px;background:var(--muted-bg)}
.wwd-phone{left:68px;top:16px;width:66px;height:148px;background:linear-gradient(180deg,#2a2a2a,#555);border-radius:9px}
.wwd-bulb{left:578px;top:20px;width:70px;height:152px;background:radial-gradient(ellipse at 50% 35%,#8a8a8a 0%,#444 55%,transparent 72%)}
.wwd-title{left:0;width:719px;top:38px;text-align:center;font-size:19px}
.wwd-text{left:180px;width:359px;top:76px;text-align:center;font-size:7.4px;line-height:12px}
.btn-outline{left:308px;top:125px;width:103px;height:26px;border:1px solid #333;font-size:10px;color:var(--ink);text-decoration:none;display:flex;align-items:center;justify-content:center}

/* services */
.services-title{left:0;width:719px;top:584px;text-align:center;font-size:19px}
.service{top:640px;width:176px;text-align:center}
.service-icon{width:92px;height:92px;border:1px solid var(--line);border-radius:50%;margin:0 auto;display:flex;align-items:center;justify-content:center}
.service-name{margin-top:11px;font-size:15.5px}
.service-text{margin-top:6px;font-size:7.4px;line-height:12px}
.service .btn-solid{width:71px;height:19px;margin:10px auto 0;font-size:7.6px}

/* testimonial */
.testimonial{left:0;top:894px;width:719px;height:276px;background:linear-gradient(90deg,#5a4636 0%,#3c3028 45%,#4a3c30 70%,#7a6450 100%)}
.testimonial-title{left:0;width:719px;top:20px;text-align:center;font-size:22px;color:var(--white)}
.avatar{left:317px;top:66px;width:84px;height:84px;border-radius:50%;border:2px solid var(--white);background:linear-gradient(180deg,#d9d9d9,#6b6f78)}
.person{left:0;width:719px;top:154px;text-align:center;color:var(--white)}
.person-name{font-weight:700;font-size:17px}
.person-role{font-size:8.5px;margin-top:0}
.person-email{font-size:8.5px;margin-top:2px}
.quote{left:120px;width:479px;top:208px;text-align:center;font-size:8px;line-height:13px;color:#eee}

/* footer */
.site-footer{left:0;top:1170px;width:719px;height:30px;background:var(--footer)}
.copyright{left:66px;top:9px;font-size:7.6px;color:#ddd}
.social{right:73px;top:7px;display:flex;gap:3px}
.social span{width:14px;height:14px;border-radius:50%;background:var(--white)}
</style>
</head>
<body>

<header class="site-header">
  <div class="abs brand">
    <span class="brand-mark"></span>
    <span class="brand-name">BRIGHTQUOKKA</span>
  </div>
  <div class="abs contact-line contact-email">
    <svg width="16" height="10" viewBox="0 0 16 10"><rect x="5" y="1" width="10" height="8" fill="none" stroke="#222"/><path d="M5 1l5 4 5-4" fill="none" stroke="#222"/><path d="M0 3h4M1 6h3" stroke="#222"/></svg>
    hello@brightquokka.net
  </div>
  <div class="abs contact-line contact-phone">
    <svg width="14" height="12" viewBox="0 0 14 12"><path d="M3 1c-2 1-2 3 0 6s5 4 7 3l1-2-2-1-1 1c-1 0-3-2-3-3l1-1-1-2z" fill="#222"/></svg>
    (0800) 314.592.607
  </div>
  <nav class="abs main-nav">
    <a class="active" href="#">Home</a>
    <a href="#">About Us</a>
    <a href="#">Shop now</a>
    <a href="#">Services</a>
    <a href="#">Contact Us</a>
  </nav>
</header>

<section class="abs hero">
  <div class="abs hero-product" role="img" aria-label="Smartphone with lighting app under a glowing green LED bulb"></div>
  <h2 class="abs heading hero-welcome">Welcome</h2>
  <h1 class="abs heading hero-title">Bright Quokka</h1>
  <p class="abs heading hero-sub">Sed ut perspiciatis unde omnis iste natus error sit voluptatema</p>
  <a class="abs btn-solid hero-btn" href="#">Read More</a>
</section>

<section class="abs what-we-do">
  <div class="abs wwd-phone" role="img" aria-label="Smartphone showing the bulb control app"></div>
  <div class="abs wwd-bulb" role="img" aria-label="Silver LED light bulb"></div>
  <h2 class="abs heading wwd-title">What We Do</h2>
  <p class="abs wwd-text">Sed ut perspiciatis unde omnis iste natus error sit voluptatem accusantium doloremque laudantium, totam rem aperiam, eaque ipsa quae ab illo inventore veritatis et quasi architecto beatae vitae dicta sunt explicabo Nemo enim ipsam</p>
  <a class="abs btn-outline" href="#">Read More</a>
</section>

<h2 class="abs heading services-title">Our Services</h2>

<div class="abs service" style="left:61px">
  <div class="service-icon">
    <svg width="34" height="54" viewBox="0 0 34 54" fill="none" stroke="#3aa646" stroke-width="3" stroke-linecap="round">
      <path d="M6 6l22-4M6 14l22-6M6 22l22-6M6 28l22-4"/>
      <path d="M9 30c0 6 4 8 4 12h8c0-4 4-6 4-12"/>
      <path d="M13 46h8v4h-8z" fill="#3aa646"/>
    </svg>
  </div>
  <h3 class="heading service-name">Led light Bulbs</h3>
  <p class="service-text">Sed ut perspiciatis unde omnis iste natus error sit totam rem aperiam, eaque ipsa quae ab illo et quasi architecto beatae vitae dicta sunt explicabo.</p>
  <a class="btn-solid" href="#">Read More</a>
</div>

<div class="abs service" style="left:271px">
  <div class="service-icon">
    <svg width="56" height="56" viewBox="0 0 56 56" fill="#3aa646">
      <circle cx="28" cy="4" r="3"/><circle cx="16" cy="8" r="2.5"/><circle cx="40" cy="8" r="2.5"/>
      <circle cx="8" cy="18" r="2.5"/><circle cx="48" cy="18" r="2.5"/><circle cx="5" cy="30" r="2.5"/><circle cx="51" cy="30" r="2.5"/>
      <circle cx="22" cy="13" r="2"/><circle cx="34" cy="13" r="2"/><circle cx="12" cy="38" r="2"/><circle cx="44" cy="38" r="2"/>
      <path d="M28 16a12 12 0 0 0-8 21c2 2 3 4 3 6h10c0-2 1-4 3-6a12 12 0 0 0-8-21zm0 4a8 8 0 0 1 5 14c-2 2-3 3-3 5h-4c0-2-1-3-3-5a8 8 0 0 1 5-14z"/>
      <rect x="23" y="45" width="10" height="3"/><rect x="24" y="50" width="8" height="3"/>
    </svg>
  </div>
  <h3 class="heading service-name">Led light color</h3>
  <p class="service-text">Sed ut perspiciatis unde omnis iste natus error sit totam rem aperiam, eaque ipsa quae ab illo et quasi architecto beatae vitae dicta sunt explicabo.</p>
  <a class="btn-solid" href="#">Read More</a>
</div>

<div class="abs service" style="left:482px">
  <div class="service-icon">
    <svg width="48" height="48" viewBox="0 0 48 48" fill="#3aa646">
      <rect x="0" y="0" width="12" height="12" rx="2"/><rect x="18" y="0" width="12" height="12" rx="2"/><rect x="36" y="0" width="12" height="12" rx="2"/>
      <rect x="0" y="18" width="12" height="12" rx="2"/><rect x="18" y="18" width="12" height="12" rx="2"/><rect x="36" y="18" width="12" height="12" rx="2"/>
      <rect x="0" y="36" width="12" height="12" rx="2"/><rect x="18" y="36" width="12" height="12" rx="2"/><rect x="36" y="36" width="12" height="12" rx="2"/>
    </svg>
  </div>
  <h3 class="heading service-name">Led Application</h3>
  <p class="service-text">Sed ut perspiciatis unde omnis iste natus error sit totam rem aperiam, eaque ipsa quae ab illo et quasi architecto beatae vitae dicta sunt explicabo.</p>
  <a class="btn-solid" href="#">Read More</a>
</div>

<section class="abs testimonial">
  <h2 class="abs heading testimonial-title">Testmonial</h2>
  <div class="abs avatar" role="img" aria-label="Portrait photo of the reviewer"></div>
  <div class="abs person">
    <div class="person-name">Daniel Marsh</div>
    <div class="person-role">Lorem ipsum dolor sit amet elit</div>
    <div class="person-email">daniel@marshmail.net</div>
  </div>
  <p class="abs quote">Lorem ipsum dolor sit amet, consectetur adipisicing elit, sed do eiusmod tempor incididunt ut labore et dolore magna aliqua. Ut enim ad minim veniam, quis nostrud exercitation ullamco laboris nisi ut aliquip ex ea commodo consequat. Duis aute irure dolor in reprehenderit in voluptate velit esse cillum dolore eu fugiat nulla pariatur .</p>
</section>

<footer class="abs site-footer">
  <p class="abs copyright">© 2014 brightquokka. All rights reserved</p>
  <div class="abs social" aria-label="Social links">
    <span></span><span></span><span></span><span></span><span></span>
  </div>
</footer>

</body>
</html>
```